KVM Contracting services . Building and maintenance services, optic fibre installation

Business cards and logo design.I need a logo that I can use on business cards ,workwear and on my vehicles. I would like the KVM to be the main or larger text and contracting services to be the smaller or less important text.I like monograms, modern designs and repeating patterns symbols. I am also a Gemini and my favourite number is 22 so if this can be any inspiration to help with the design. Am thinking of the using German flag colours as a his is my family’s heritage. And the other 2 main colours I wear is black and white.But any ideas are appreciated.I do not need a design that is trade specific but a design that could be used for any business.

Target Market(s)

General public

Contact Information for Business Card

KVM Contracting Services ( front of business card)

(Back of business card)
Darren Holtwick
0451907326
Maintenance services
Optic fibre and data installation

Logo Text

Logo can just be pattern or monogram or incorporate KVM . I like the gemini star sign and the number 22

Colors
ec1f27
000000
fbee3e
ffffff

Requirements
Must have
• Logo and KVM Contracting Services on the front of business card
Nice to have
• Possible use of German flag colours.
• Modern design.
• Design to be able to be used on black or white background as I want to put it on clothing

```html
<!DOCTYPE html>
<html lang="en">
<head>
<meta charset="utf-8">
<title>KVM Contracting Services – Business Card</title>
<link rel="stylesheet" href="https://fonts.googleapis.com/css2?family=Lato:wght@400;700;900&display=swap">
<style>
  :root {
    --page-bg: #1b1b1d;
    --card-bg: #141414;
    --card-edge: #262626;
    --brand-red: #e3202a;
    --text-white: #f2f2f2;
    --logo-silver: #c9c9c9;
    --rule-white: #e8e8e8;
  }
  * { box-sizing: border-box; margin: 0; padding: 0; }
  html, body {
    width: 1200px; height: 900px; overflow: hidden;
    background: var(--page-bg);
    font-family: "Lato", Arial, sans-serif;
  }
  .canvas {
    position: relative; width: 1200px; height: 900px;
    display: flex; flex-direction: column; align-items: center; justify-content: center; gap: 40px;
  }
  .card {
    width: 680px; height: 390px;
    background: linear-gradient(135deg, #111 0%, var(--card-bg) 55%, #1f1f1f 100%);
    border: 1px solid var(--card-edge);
    position: relative;
  }
  .card-front { display: flex; align-items: center; justify-content: center; }
  .wordmark { font-weight: 900; text-transform: uppercase; line-height: 1; }
  .wordmark-main { display: block; letter-spacing: 2px; }
  .wordmark-sub { display: block; letter-spacing: 3px; }
  .card-front .wordmark { color: var(--logo-silver); text-align: center; }
  .card-front .wordmark-main { font-size: 110px; }
  .card-front .wordmark-sub { font-size: 22px; margin-top: 8px; }

  .card-back { display: flex; align-items: center; padding: 0 40px 0 52px; }
  .card-back .wordmark { color: var(--brand-red); width: 250px; }
  .card-back .wordmark-main { font-size: 84px; }
  .card-back .wordmark-sub { font-size: 16px; margin-top: 6px; letter-spacing: 1.5px; }
  .divider { width: 2px; height: 170px; background: var(--rule-white); margin: 0 34px 0 20px; }
  .contact { color: var(--text-white); font-size: 19px; }
  .contact-name { color: var(--brand-red); font-size: 28px; font-weight: 400; text-transform: uppercase; letter-spacing: 0.5px; }
  .contact-role { font-size: 19px; margin-bottom: 18px; }
  .contact-address { line-height: 1.3; margin-bottom: 12px; }
  .contact-line { display: flex; align-items: center; gap: 10px; line-height: 1.35; }
  .contact-line svg { width: 13px; height: 13px; flex: none; }
</style>
</head>
<body>
<main class="canvas">
  <section class="card card-front">
    <p class="wordmark">
      <span class="wordmark-main">KVM</span>
      <span class="wordmark-sub">Contracting Services</span>
    </p>
  </section>

  <section class="card card-back">
    <p class="wordmark">
      <span class="wordmark-main">KVM</span>
      <span class="wordmark-sub">Contracting Services</span>
    </p>
    <div class="divider"></div>
    <div class="contact">
      <p class="contact-name">Darren Holtwick</p>
      <p class="contact-role">Director</p>
      <p class="contact-address">18 Larkspur Road,<br>Maple Grove, FL 32100, USA</p>
      <p class="contact-line">
        <svg viewBox="0 0 24 24" aria-hidden="true"><path fill="#e3202a" d="M6.6 10.8a15 15 0 0 0 6.6 6.6l2.2-2.2a1 1 0 0 1 1-.25 11.4 11.4 0 0 0 3.6.57 1 1 0 0 1 1 1V20a1 1 0 0 1-1 1A17 17 0 0 1 3 4a1 1 0 0 1 1-1h3.5a1 1 0 0 1 1 1c0 1.25.2 2.45.57 3.57a1 1 0 0 1-.25 1z"/></svg>
        0451907326
      </p>
      <p class="contact-line">
        <svg viewBox="0 0 24 24" aria-hidden="true"><rect x="2" y="5" width="20" height="14" fill="none" stroke="#e3202a" stroke-width="2"/><path d="M2 5l10 8 10-8" fill="none" stroke="#e3202a" stroke-width="2"/></svg>
        info@kvmcontracting.com
      </p>
      <p class="contact-line">
        <svg viewBox="0 0 24 24" aria-hidden="true"><g fill="none" stroke="#e3202a" stroke-width="2"><circle cx="12" cy="12" r="10"/><ellipse cx="12" cy="12" rx="4.5" ry="10"/><path d="M2 12h20"/></g></svg>
        www.kvmcontracting.com
      </p>
    </div>
  </section>
</main>
</body>
</html>
```